Veldmark Supplies Business Card

Professional business card that stand out to our potential customers. Front and back with clean modern design

Industry/Entity Type

Oil and gas

Contact Information for Business Card

Name, address, website , office phone and cell number

Requirements
Must have
• Editable files for each employee

```html
<!DOCTYPE html>
<html lang="en">
<head>
<meta charset="utf-8">
<title>Veldmark Supplies Business Card</title>
<link href="https://fonts.googleapis.com/css2?family=Poppins:wght@400;500;600;700&display=swap" rel="stylesheet">
<style>
  :root {
    --red: #e8262a;
    --blue: #13afd2;
    --ink: #1b1b1b;
    --paper: #ffffff;
    --backdrop: #e2e6e8;
  }
  * { margin: 0; padding: 0; box-sizing: border-box; }
  html, body {
    width: 1200px; height: 960px; overflow: hidden;
    background: var(--backdrop);
    font-family: "Poppins", sans-serif;
  }
  .card {
    position: absolute;
    left: 250px; width: 702px; height: 401px;
    background: var(--paper);
    border-radius: 30px;
    overflow: hidden;
  }
  .card--front { top: 60px; }
  .card--back { top: 500px; }
  .card__band {
    position: absolute; left: 0; right: 0; bottom: 0; height: 24px;
    background: var(--red);
    border-top: 2px solid var(--blue);
  }
  .brand {
    position: absolute;
    display: flex; align-items: center;
    color: var(--red); font-weight: 600; white-space: nowrap;
  }
  .brand__square { background: var(--red); flex: none; }
  .brand--front {
    left: 0; right: 0; top: 160px; justify-content: center;
    font-size: 42px; gap: 16px;
  }
  .brand--front .brand__square { width: 34px; height: 34px; }
  .brand--back {
    left: 46px; top: 180px; font-size: 25px; gap: 10px;
  }
  .brand--back .brand__square { width: 20px; height: 20px; }
  .connector { position: absolute; left: 340px; top: 58px; }
  .contact { position: absolute; left: 418px; top: 86px; }
  .contact__name { font-size: 33px; line-height: 1.1; white-space: nowrap; }
  .contact__first { color: var(--red); font-weight: 700; }
  .contact__last { color: var(--blue); font-weight: 400; }
  .contact__role { font-size: 16.5px; font-weight: 500; color: var(--ink); margin-top: 6px; }
  .contact__address { font-size: 16.5px; color: var(--blue); line-height: 22px; margin-top: 12px; letter-spacing: 0.3px; }
  .contact__list { list-style: none; margin-top: 12px; }
  .contact__item {
    display: flex; align-items: center; gap: 12px;
    font-size: 17px; color: var(--ink); line-height: 22px;
  }
  .contact__icon { width: 17px; height: 17px; flex: none; }
</style>
</head>
<body>
  <section class="card card--front">
    <div class="brand brand--front"><span class="brand__square"></span>Veldmark Supplies</div>
    <div class="card__band"></div>
  </section>

  <section class="card card--back">
    <div class="brand brand--back"><span class="brand__square"></span>Veldmark Supplies</div>

    <svg class="connector" width="140" height="282" viewBox="0 0 140 282" fill="none">
      <path d="M129 8 H16 Q9 8 9 15 V261 Q9 268 16 268 H129" stroke="var(--red)" stroke-width="2"/>
      <path d="M9 142 H47" stroke="var(--red)" stroke-width="2"/>
      <circle cx="129" cy="8" r="4.5" fill="var(--red)"/>
      <circle cx="47" cy="142" r="4.5" fill="var(--red)"/>
      <circle cx="129" cy="268" r="4.5" fill="var(--red)"/>
    </svg>

    <div class="contact">
      <h1 class="contact__name"><span class="contact__first">Marela</span> <span class="contact__last">Kostova</span></h1>
      <p class="contact__role">Co-Founder &amp; CEO</p>
      <p class="contact__address">418 Ridgeline Avenue,<br>Carrow, TX 79701</p>
      <ul class="contact__list">
        <li class="contact__item">
          <svg class="contact__icon" viewBox="0 0 24 24"><path d="M6 3l3 5-2 2c1 3 3 5 6 6l2-2 5 3-2 4C10 21 3 14 3 5z" fill="var(--blue)"/></svg>
          (555) 214-6083
        </li>
        <li class="contact__item">
          <svg class="contact__icon" viewBox="0 0 24 24"><rect x="6" y="2" width="12" height="20" rx="2" fill="none" stroke="var(--red)" stroke-width="2.4"/></svg>
          (555) 730-4419
        </li>
        <li class="contact__item">
          <svg class="contact__icon" viewBox="0 0 24 24"><circle cx="12" cy="12" r="10" fill="var(--blue)"/><path d="M2 12h20M12 2c4 4 4 16 0 20M12 2c-4 4-4 16 0 20" stroke="#fff" stroke-width="1.4" fill="none"/></svg>
          www.veldmarksupplies.com
        </li>
        <li class="contact__item">
          <svg class="contact__icon" viewBox="0 0 24 24"><rect x="2" y="8" width="20" height="14" fill="var(--red)"/><path d="M2 8l10 8 10-8" stroke="#fff" stroke-width="1.5" fill="none"/></svg>
          info@veldmarksupplies.com
        </li>
      </ul>
    </div>
    <div class="card__band"></div>
  </section>
</body>
</html>
```